Mela and Dorvan Destination Wedding Invitation

THE DESIGN
- We need a unique, fun and colourful wedding invitation.
- We would like the designs to be printed using letterpress (not block) and or laser cut. Open to suggestions.
- We would like to include the attached wedding logo.
- We would like a design that is fun yet classy.
- 3D if possible.
- Main colour: deep purple; secondary colour: green.

Colour example:
http://www.vowplume.com/Soft-Bloom-Tansy-Heather-Posyq/tkrmz482.htm
- we did think about using the following product to enclose the necessary cards. This is not mandatory. http://www.wedlockparcel.co.uk/product/fern-leaf-invitation#colour=19

TO AVOID
- Paisleys
- Obvious flowers
- Block letterpress

FAVOURED DESIGNS
http://i0.wp.com/www.inkfolly.com/images/blog-images/fern-lantern1.jpg?resize=400%2C533
http://studiovorland.com/collection-brevin.html
http://studiovorland.com/collection-tamsel.html
https://www.craftloom.com/listing/418207395/fenwick-wedding-invitation-laser-cut

THE COUPLE
- Bride: Mela Joan Castrillo
- Groom: Dorvan Pilcher
- Both from Sydney, Australia
- Both living in London, UK
- Website: melaanddorvan.com

THE WEDDING:
- We are getting married in Koh Samui, Thailand, early next year.
- We have 3 official events, the welcome drinks (March 25), the wedding (March 27) and beach bbq (March 28).

THE INVITE -1 CARD design
For everyone, a page/card that will include the following:
- Reception/ Main invite
- Location card (Direction/Map). Venue: Thonburee Lagoon Spa Resort
- RSVP - via website
See wording attachment for details.

I need an insert (template) for the following: - 1 design only.
- Tide Glow Social
- Tot Haven (for people with children)
- Rehearsal

ADDITIONAL
- We would like the design to be adaptable for place cards and or wedding programs (normal printer).

Please let me know if you need more information.
Updates

Target Market(s)

Fun, casual, unique

Industry/Entity Type

Wedding

Colors
6b449b
876aae
b7a5cd

Requirements
Must have
• Wedding logo
Nice to have
• Please see project description
Should not have

```html
<!DOCTYPE html>
<html lang="en">
<head>
<meta charset="utf-8">
<title>Mela &amp; Dorvan – Wedding Invitation</title>
<link rel="stylesheet" href="https://fonts.googleapis.com/css2?family=Great+Vibes&family=Parisienne&display=swap">
<style>
  :root {
    --purple-deep: #5e3594;
    --purple-main: #6b449b;
    --purple-mid: #876aae;
    --purple-light: #b7a5cd;
    --text-white: #ffffff;
    --accent-gold: #f29a2e;
  }
  * { margin: 0; padding: 0; box-sizing: border-box; }
  html, body { width: 833px; height: 1200px; overflow: hidden; background: var(--purple-main); }
  .invitation {
    position: relative;
    width: 833px; height: 1200px;
    background: radial-gradient(ellipse at 50% 50%, var(--purple-main) 0%, var(--purple-deep) 100%);
    color: var(--text-white);
    font-family: "Parisienne", cursive;
    overflow: hidden;
  }
  .border-ornament { position: absolute; left: 0; width: 833px; }
  .border-ornament--top {
    top: 0; height: 200px;
    background: linear-gradient(180deg, var(--purple-light) 0%, var(--purple-mid) 55%, rgba(135,106,174,0) 100%);
    clip-path: polygon(0 0, 100% 0, 100% 60%, 75% 75%, 60% 100%, 50% 85%, 40% 100%, 25% 75%, 0 60%);
  }
  .border-ornament--bottom {
    bottom: 0; height: 190px;
    background: linear-gradient(0deg, var(--purple-light) 0%, var(--purple-mid) 55%, rgba(135,106,174,0) 100%);
    clip-path: polygon(0 40%, 25% 25%, 40% 0, 50% 15%, 60% 0, 75% 25%, 100% 40%, 100% 100%, 0 100%);
  }
  .wedding-mark {
    position: absolute; top: 222px; left: 0; width: 100%;
    text-align: center;
    font-family: "Great Vibes", cursive;
    font-size: 34px; color: var(--accent-gold);
  }
  .couple { position: absolute; top: 322px; left: 0; width: 100%; }
  .couple__person { position: absolute; text-align: center; width: 330px; }
  .couple__person--bride { left: 60px; }
  .couple__person--groom { left: 443px; }
  .couple__name {
    font-family: "Great Vibes", cursive;
    font-weight: 400;
    font-size: 46px; line-height: 48px;
    white-space: nowrap;
  }
  .couple__parents { font-size: 19px; margin-top: 14px; white-space: nowrap; }
  .couple__amp {
    position: absolute; left: 0; width: 100%; top: 2px;
    text-align: center;
    font-family: "Great Vibes", cursive; font-size: 52px;
  }
  .intro {
    position: absolute; top: 520px; width: 100%;
    text-align: center; font-size: 24px; line-height: 34px;
  }
  .star { position: absolute; left: 408px; width: 18px; height: 18px; }
  .events { position: absolute; top: 620px; left: 110px; width: 700px; }
  .event { display: flex; height: 88px; white-space: nowrap; }
  .event__date { width: 220px; }
  .event__day { font-size: 22px; line-height: 26px; }
  .event__time { font-size: 34px; line-height: 40px; }
  .event__time sup { font-size: 16px; }
  .event__details { padding-top: 4px; font-size: 17px; line-height: 24px; }
  .closing {
    position: absolute; top: 892px; width: 100%;
    text-align: center; font-size: 22px; line-height: 31px;
  }
  .rsvp {
    position: absolute; top: 990px; width: 100%;
    text-align: center; font-size: 21px; white-space: nowrap;
  }
</style>
</head>
<body>
<main class="invitation">
  <div class="border-ornament border-ornament--top" role="img" aria-label="Lavender filigree border ornament along the top edge"></div>

  <div class="wedding-mark">Mela &amp; Dorvan</div>

  <section class="couple">
    <div class="couple__person couple__person--bride">
      <h1 class="couple__name">Mela Joan<br>Castrillo</h1>
      <p class="couple__parents">Daughter of Corazon and Benito</p>
    </div>
    <div class="couple__amp">&amp;</div>
    <div class="couple__person couple__person--groom">
      <h1 class="couple__name">Dorvan Emil<br>Pilcher</h1>
      <p class="couple__parents">Son of Lorna and Halvard</p>
    </div>
  </section>

  <p class="intro">Please join us for a celebration of love,<br>friendship, laughter and family</p>

  <svg class="star" style="top:596px" viewBox="0 0 20 20" aria-hidden="true"><polygon points="10,1 12.5,7.5 19,7.5 13.8,11.8 15.8,18.5 10,14.5 4.2,18.5 6.2,11.8 1,7.5 7.5,7.5" fill="var(--accent-gold)"/></svg>

  <section class="events">
    <div class="event">
      <div class="event__date">
        <div class="event__day">march friday</div>
        <div class="event__time">25<sup>th</sup> 6:00pm</div>
      </div>
      <div class="event__details">Welcome drinks and canapes<br>Thonburee Lagoon Spa Resort, Surat, Koh Samui, Thailand</div>
    </div>
    <div class="event">
      <div class="event__date">
        <div class="event__day">march sunday</div>
        <div class="event__time">27<sup>th</sup> 4:00pm</div>
      </div>
      <div class="event__details">Wedding ceremony and reception<br>Thonburee Lagoon Spa Resort, Surat, Koh Samui, Thailand</div>
    </div>
    <div class="event">
      <div class="event__date">
        <div class="event__day">march monday</div>
        <div class="event__time">28<sup>th</sup> 1:00pm</div>
      </div>
      <div class="event__details">Beach BBQ Lunch<br>Thonburee Lagoon Spa Resort, Surat, Koh Samui, Thailand</div>
    </div>
  </section>

  <p class="closing">Fabulous food, fun and festivities to follow.<br>Wedding ceremony dress code: colourful beach formal</p>

  <svg class="star" style="top:962px" viewBox="0 0 20 20" aria-hidden="true"><polygon points="10,1 12.5,7.5 19,7.5 13.8,11.8 15.8,18.5 10,14.5 4.2,18.5 6.2,11.8 1,7.5 7.5,7.5" fill="var(--accent-gold)"/></svg>

  <p class="rsvp">Please RSVP by 1st November 2015 via website: melaanddorvan.com</p>

  <div class="border-ornament border-ornament--bottom" role="img" aria-label="Lavender filigree border ornament along the bottom edge"></div>
</main>
</body>
</html>
```